Quillmere Supply Chain and Logistic Consulting

Please review the attached Business Card. I want as close to this card with the colors, fonts, and quality of the card as possible. The attached compass should replace the deer head on both sides of the card and the text should say:

Backside
Compass JPEG
Quillmere SC&L
A Supply Chain and Logistics Consulting Company

Frontside
Quillmere SC&L
Ray Falkner - Brennock Bay
President
____________________________________
(555) 314-9027
QuillmereSCL@Examplemail.com
_____________________________________

Bottom Front Side

Target Market(s)

Businesses

Contact Information for Business Card

Backside
Compass JPEG
Quillmere SC&L

Frontside
Quillmere SC&L
President
(555) 314-9027
QuillmereSCL@Examplemail.com

Bottom Front Side

Font styles to use
Serif
Script

Colors

Designer to choose colors to be used in the design.

Requirements
Must have
• See attached card for reference
Nice to have
Should not have

```html
<!DOCTYPE html>
<html lang="en">
<head>
<meta charset="utf-8">
<title>Quillmere SC&amp;L – Business Card</title>
<link rel="stylesheet" href="https://fonts.googleapis.com/css2?family=Cinzel:wght@400;500;600&family=Libre+Baskerville:wght@400;700&display=swap">
<style>
  :root {
    --backdrop: #e4e5e8;
    --card-navy: #0c2a4b;
    --card-ink: #ffffff;
    --card-muted: rgba(255, 255, 255, 0.85);
    --rule: rgba(255, 255, 255, 0.55);
    --mark-faint: rgba(255, 255, 255, 0.08);
    --card-shadow: 0 14px 30px rgba(20, 30, 45, 0.22);
  }
  * { box-sizing: border-box; margin: 0; padding: 0; }
  html, body {
    width: 1200px;
    height: 900px;
    overflow: hidden;
    background: var(--backdrop);
  }
  .canvas {
    position: relative;
    width: 1200px;
    height: 900px;
  }
  .card {
    position: absolute;
    width: 600px;
    height: 343px;
    border-radius: 26px;
    background: var(--card-navy);
    box-shadow: var(--card-shadow);
    color: var(--card-ink);
    overflow: hidden;
    text-align: center;
  }
  .card--back { left: 100px; top: 90px; }
  .card--front { left: 500px; top: 467px; }

  .brand-mark {
    position: absolute;
    border-radius: 50%;
  }
  .card--back .brand-mark {
    width: 124px;
    height: 124px;
    left: 238px;
    top: 40px;
    border: 2px solid var(--card-ink);
  }
  .card--front .brand-mark {
    width: 300px;
    height: 300px;
    left: 150px;
    top: 22px;
    border: 2px solid var(--mark-faint);
  }

  .company-name {
    font-family: "Cinzel", serif;
    font-weight: 500;
    letter-spacing: 0.04em;
  }
  .card--back .company-name {
    position: absolute;
    left: 0; right: 0;
    top: 196px;
    font-size: 26px;
  }
  .tagline {
    position: absolute;
    left: 0; right: 0;
    font-family: "Cinzel", serif;
    font-weight: 400;
    font-size: 16px;
    letter-spacing: 0.05em;
    color: var(--card-muted);
  }
  .card--back .tagline { top: 286px; }
  .card--front .tagline { top: 294px; }

  .contact-block {
    position: absolute;
    left: 0; right: 0;
    top: 40px;
    display: flex;
    flex-direction: column;
    align-items: center;
  }
  .card--front .company-name {
    font-size: 38px;
    line-height: 1.1;
  }
  .person-line {
    margin-top: 14px;
    font-family: "Libre Baskerville", serif;
    font-weight: 700;
    font-size: 19px;
  }
  .person-role {
    margin-top: 2px;
    font-family: "Libre Baskerville", serif;
    font-size: 13px;
    color: var(--card-muted);
  }
  .rule {
    width: 250px;
    height: 1px;
    background: var(--rule);
    margin: 8px 0;
  }
  .contact-item {
    font-family: "Libre Baskerville", serif;
    font-size: 14px;
    line-height: 1.55;
  }
</style>
</head>
<body>
<main class="canvas">

  <section class="card card--back" aria-label="Business card back">
    <div class="brand-mark" aria-hidden="true"></div>
    <h1 class="company-name">QUILLMERE SC&amp;L</h1>
    <p class="tagline">A Supply Chain and Logistics Consulting Company</p>
  </section>

  <section class="card card--front" aria-label="Business card front">
    <div class="brand-mark" aria-hidden="true"></div>
    <div class="contact-block">
      <h2 class="company-name">QUILLMERE SC&amp;L</h2>
      <p class="person-line">Ray Falkner - Brennock Bay</p>
      <p class="person-role">President</p>
      <div class="rule"></div>
      <p class="contact-item">(555) 314-9027</p>
      <p class="contact-item">QuillmereSCL@Examplemail.com</p>
      <div class="rule"></div>
    </div>
    <p class="tagline">A Supply Chain and Logistics Consulting Company</p>
  </section>

</main>
</body>
</html>
```